Maple Beacon Website

We are starting a marketing company and to do that we need a website! We want a website that will inspire and persuade to bring out the awesomeness in our clients.
What we want to see:
- Inspirational and persuasive imagery that relate to Branding.
- No cliche images eg. business man, suits and hand shakes
- We want to transform and educate our clients.
- We want to show them the path and would like our website to really act as a guide that guides them step by step through our process.
- We want the portray that we are an investment but not have a pretentious way to it. We put our heart into every project and that is how we treat our clients.
-When you submit your design please include what platform you have created for. Preference would be Wordpress or Joobla.

We have included the psd file for the wire frame, logo files, font files, site map and a link to a video we create to give you more information on what we would like to see. http://clipvault.example/t/qk82LmZpr

Feel free to make small modification to the logos if you think it will improve it. Your creativity and advice is most welcome.
Updates

One thing we forgot. We would like to have our contact information near the top of the website as well as at the bottom.  Here is out contact info:

Email: info@maplebeacon.example
Phone: 587-555-0142

Project Deadline Extended
Reason: As we are new with the platform and that we want to optimize our results, we decided to extend the deadline by 15 days. Thanks!

Target Market(s)

28-60, Male and Female, Oil field, Local Businesses, Dentists, Chiropractors, Hair salon, Construction/Renovation, Events etc

Industry/Entity Type

Investment

Requirements
Must have
• - 4 Inspirational and persuasive Imagery for the top portion of the website
- Must have a feel as if your not on a website an example of this is linked below.
http://www.artbidhub.example/design/402957/web-design-by-lena-torvik
Nice to have
• - Creative advice from you.
- Creative buttons for Get Free Quote and Subscribe buttons. Something out of the box that draws peoples attention. eg. a 'B' button. Just and example but still something related to branding.
Should not have
• No Cliches

```html
<!DOCTYPE html>
<html lang="en">
<head>
<meta charset="utf-8">
<title>Maple Beacon</title>
<link rel="stylesheet" href="https://fonts.googleapis.com/css2?family=Signika:wght@400;600;700&family=Open+Sans:ital,wght@0,400;0,600;0,700;1,400&display=swap">
<style>
:root{
  --green-dark:#4f7a2a;
  --green-bright:#8cb43a;
  --green-btn-top:#a6cc4c;
  --green-btn-bottom:#7fa832;
  --green-text:#8ab32e;
  --grey-tab-top:#b4b5b7;
  --grey-tab-bottom:#8d8e91;
  --ink:#3d3d3d;
  --body-text:#555;
  --box-bg:#f5f5f5;
  --box-border:#e6e6e6;
  --strip-bg:#d6d6d6;
  --page-bg:#fafafa;
  --footer-bg:#4a4a4a;
  --footer-text:#e8e8e8;
  --white:#fff;
}
*{box-sizing:border-box;margin:0;padding:0}
html,body{width:1200px;height:1020px;overflow:hidden}
body{position:relative;background:var(--page-bg);font-family:"Open Sans",sans-serif;color:var(--body-text)}
.abs{position:absolute}

.hero{left:0;top:0;width:1200px;height:448px;
  background:linear-gradient(180deg,#f0f0f0 0,#e6e6e6 55%,#dcdedb 74%,#e9ebe6 100%)}

.logo{left:130px;top:36px;display:flex;align-items:center;gap:10px}
.logo-mark{width:20px;height:20px;background:var(--green-bright)}
.logo-name{font-family:"Signika",sans-serif;font-weight:700;font-size:38px;color:#6f6f6f;letter-spacing:.5px}
.tagline{left:161px;top:101px;font-style:italic;font-size:14px;color:var(--ink)}

.tabs{left:370px;top:82px;display:flex;gap:15px}
.tab{position:relative;width:164px;height:45px;border-radius:3px;display:flex;align-items:center;justify-content:center;
  font-family:"Signika",sans-serif;font-weight:700;font-size:18px;color:var(--white);letter-spacing:.3px;
  background:linear-gradient(var(--grey-tab-top),var(--grey-tab-bottom));text-shadow:0 1px 1px rgba(0,0,0,.35)}
.tab.active{background:linear-gradient(var(--green-btn-top),var(--green-btn-bottom))}
.tab.active::after{content:"";position:absolute;left:72px;bottom:-10px;border:10px solid transparent;border-bottom:0;border-top-color:var(--green-btn-bottom)}

.side-menu{left:130px;top:142px;width:220px;height:260px;background:rgba(79,122,42,.93);border-radius:3px;list-style:none;padding-top:16px}
.side-menu li{height:50px;line-height:28px;padding-left:44px;position:relative;font-family:"Signika",sans-serif;font-weight:700;font-size:15px;color:var(--white);letter-spacing:.6px}
.side-menu li.current::before{content:"";position:absolute;left:18px;top:10px;width:9px;height:9px;border-radius:50%;background:var(--green-btn-top)}

.hero-title{right:128px;top:356px;font-family:"Signika",sans-serif;font-weight:700;font-size:50px;color:var(--white);letter-spacing:2px;text-shadow:2px 2px 3px rgba(0,0,0,.45)}

.strip{background:var(--strip-bg);box-shadow:0 10px 10px -8px rgba(0,0,0,.35)}
.connect{left:130px;top:461px;width:220px;height:97px;text-align:center}
.strip-title{font-family:"Signika",sans-serif;font-weight:700;font-size:20px;color:var(--ink);letter-spacing:.6px;margin-top:12px}
.social{display:flex;gap:9px;justify-content:center;margin-top:11px}
.social span{width:30px;height:30px;border-radius:3px;background:#8a8a8a}
.newsletter{left:371px;top:461px;width:699px;height:97px;text-align:center}
.newsletter .accent{color:var(--green-dark)}
.subscribe-row{display:flex;gap:10px;justify-content:center;margin-top:12px}
.field{background:var(--white);border:1px solid #ccc;border-radius:4px;box-shadow:inset 0 1px 3px rgba(0,0,0,.12)}
.subscribe-row .field{width:405px;height:34px}
.btn{display:inline-flex;align-items:center;justify-content:center;background:linear-gradient(var(--green-btn-top),var(--green-btn-bottom));border:1px solid #6f9a2a;border-radius:3px;
  font-family:"Signika",sans-serif;font-weight:700;color:var(--white);text-shadow:0 1px 1px rgba(0,0,0,.3)}
.subscribe-row .btn{width:123px;height:34px;font-size:17px;letter-spacing:.5px}

.card{background:var(--box-bg);border:3px solid var(--box-border)}
.welcome{left:130px;top:593px;width:620px;height:320px;padding:11px 21px}
.quote{left:770px;top:593px;width:300px;height:320px;padding:11px 10px 11px 19px}
.card h2{font-family:"Signika",sans-serif;font-weight:700;font-size:23px;line-height:30px;color:var(--green-dark)}
.lead{margin-top:8px;font-size:13px;line-height:20px;font-weight:600;color:var(--green-text)}
.copy{margin-top:7px;width:570px;font-size:12.2px;line-height:23px;color:var(--body-text)}
.welcome .btn{position:absolute;left:21px;top:262px;width:101px;height:29px;font-size:15px}
.quote-intro{margin-top:4px;width:265px;font-size:12px;font-style:italic;line-height:15px;color:var(--ink)}
.quote .field{width:252px;height:27px;margin-top:9px;font-size:11px;font-style:italic;color:#999;padding:5px 12px}
.quote .field:first-of-type{margin-top:13px}
.quote .field.tall{height:59px}
.quote .btn{position:absolute;right:22px;top:279px;width:101px;height:29px;font-size:15px}

.footer{left:0;top:931px;width:1200px;height:89px;background:var(--footer-bg);text-align:center;color:var(--footer-text);font-size:10.5px}
.footer-nav{margin-top:25px;letter-spacing:.3px;word-spacing:2px}
.footer-nav span{margin:0 10px}
.copyright{margin-top:9px;color:#cfcfcf;letter-spacing:.3px}
</style>
</head>
<body>
<div class="abs hero" role="img" aria-label="Photo: a row of green apples with one red apple being picked by a hand, on a white surface"></div>

<div class="abs logo"><span class="logo-mark"></span><span class="logo-name">Maple Beacon</span></div>
<p class="abs tagline">Because You´re Awesome!</p>

<nav class="abs tabs">
  <div class="tab active">Maple Beacon</div>
  <div class="tab">Be Found</div>
  <div class="tab">Connect</div>
  <div class="tab">Get Growing</div>
</nav>

<ul class="abs side-menu">
  <li class="current">STRATEGY</li>
  <li>PORTFOLIO</li>
  <li>ABOUT US</li>
  <li>CONTACT US</li>
  <li>BLOG</li>
</ul>

<h1 class="abs hero-title">MAPLE BEACON</h1>

<section class="abs strip connect">
  <h3 class="strip-title">CONNECT WITH US</h3>
  <div class="social"><span></span><span></span><span></span><span></span><span></span></div>
</section>

<section class="abs strip newsletter">
  <h3 class="strip-title">GET TIPS AND TRICKS! <span class="accent">SUBSCRIBE TO OUR NEWSLETTER</span></h3>
  <div class="subscribe-row"><div class="field"></div><div class="btn">SUBSCRIBE</div></div>
</section>

<section class="abs card welcome">
  <h2>Welcome to Our Site</h2>
  <p class="lead">Lorem ipsum dolor sit amet, consectetur adipiscing elit. Fusce accumsan, elit a suscipit sagittis, tortor sapien cursus risus, non rhoncus lectus nunc ac nulla..</p>
  <p class="copy">Aliquam molestie, mi et imperdiet euismod, dui purus auctor tellus, et interdum lacus lectus et ante. Sed accumsan sollicitudin sapien, sit amet adipiscing turpis gravida ac. In congue, neque ac lobortis volutpat, libero mauris varius mi, vitae suscipit ipsum ligula vitae risus. Duis aliquam nibh a dui iaculis viverra id a velit. Vivamus egestas risus in magna varius commodo. Sed semper viverra egestas. Etiam pretium porttitor lectus, vel ornare neque porta volutpat. Aenean a nibh eget turpis vehicula tempus ac sed massa.</p>
  <div class="btn">Read More</div>
</section>

<section class="abs card quote">
  <h2>Get a Free Quote</h2>
  <p class="quote-intro">If you would like to more information on how we can help you achive your goals. You can visit our strategy page or simply get a free Quote !</p>
  <div class="field">Full Name</div>
  <div class="field">Email Address</div>
  <div class="field">Contact No.</div>
  <div class="field tall">Comments</div>
  <div class="btn">Submit Now</div>
</section>

<footer class="abs footer">
  <p class="footer-nav">STRATEGY<span>|</span>PORTFOLIO<span>|</span>ABOUT US<span>|</span>CONTACT US<span>|</span>BLOG<span>|</span>SITE MAP</p>
  <p class="copyright">COPYRIGHT ©2013. MAPLE BEACON INC. | ALL RIGHT RESERVED</p>
</footer>
</body>
</html>
```